Business Card Design

Company is a Commercial Building Company specialising in New Construction and existing refurbishments

Industry/Entity Type

Business

Contact Information for Business Card

Liam Porter
Construction Manager
E Liam@marshbuilding.com.au
M 0400 213 594
Mail 14 Tarrant Rise Harlow Bay WA 6290

```html
<!DOCTYPE html>
<html lang="en">
<head>
<meta charset="utf-8">
<title>Marsh Building &amp; Construction – Business Card</title>
<link href="https://fonts.googleapis.com/css2?family=Roboto:wght@300;400;500&display=swap" rel="stylesheet">
<style>
  :root {
    --navy: #12233b;
    --white: #ffffff;
    --cyan: #1bb8d8;
    --orange: #f28c1e;
    --ink: #111111;
    --backdrop: #e9e6e1;
  }
  * { margin: 0; padding: 0; box-sizing: border-box; }
  html, body {
    width: 1200px; height: 848px; overflow: hidden;
    background: var(--backdrop);
    font-family: "Roboto", Arial, sans-serif;
  }
  .stage {
    position: relative; width: 1200px; height: 848px;
    display: flex; align-items: center; justify-content: center; gap: 40px;
  }
  .card {
    position: relative; width: 540px; height: 309px;
    border-radius: 22px; overflow: hidden;
    box-shadow: 0 10px 28px rgba(0,0,0,0.18);
  }
  .card--front { background: var(--white); }
  .card--back { background: var(--navy); display: flex; align-items: center; justify-content: center; }

  .front-band { position: absolute; inset: 0; }

  .brand {
    position: absolute; top: 38px; left: 0; width: 100%;
    display: flex; align-items: center; justify-content: center; gap: 10px;
  }
  .brand__mark { width: 14px; height: 14px; background: var(--orange); }
  .brand__name {
    font-weight: 500; font-size: 17px; letter-spacing: 0.5px;
    color: var(--navy); text-transform: uppercase; line-height: 1.1;
    text-align: center;
  }
  .holder {
    position: absolute; top: 86px; left: 0; width: 100%; text-align: center; color: var(--ink);
  }
  .holder__name { font-weight: 300; font-size: 32px; line-height: 1.1; }
  .holder__role { font-weight: 400; font-size: 15px; margin-top: 3px; }

  .contact {
    position: absolute; width: 180px; text-align: center;
    color: var(--white); font-weight: 300; font-size: 14px; line-height: 1.35;
  }
  .contact__icon {
    position: absolute; left: 50%; transform: translateX(-50%);
    width: 42px; height: 42px; border-radius: 50%;
    background: var(--white); border: 3px solid var(--ink);
    display: flex; align-items: center; justify-content: center;
  }
  .contact--phone { left: 0; top: 262px; font-size: 17px; }
  .contact--phone .contact__icon { top: -77px; }
  .contact--email { left: 180px; top: 244px; font-size: 13px; }
  .contact--email .contact__icon { top: -77px; }
  .contact--address { left: 360px; top: 219px; font-size: 13px; }
  .contact--address .contact__icon { top: -71px; }

  .back-brand { display: flex; align-items: center; gap: 16px; }
  .back-brand__mark { width: 26px; height: 26px; background: var(--orange); }
  .back-brand__name {
    color: var(--white); font-weight: 500; font-size: 28px;
    letter-spacing: 1px; text-transform: uppercase; line-height: 1.15;
  }
</style>
</head>
<body>
<main class="stage">
  <section class="card card--front" aria-label="Business card front">
    <svg class="front-band" width="540" height="309" viewBox="0 0 540 309" aria-hidden="true">
      <polygon points="0,215 540,158 540,309 0,309" fill="var(--navy)"/>
    </svg>

    <div class="brand">
      <span class="brand__mark"></span>
      <span class="brand__name">Marsh Building<br>&amp; Construction</span>
    </div>

    <div class="holder">
      <div class="holder__name">Liam Porter</div>
      <div class="holder__role">Construction Manager</div>
    </div>

    <div class="contact contact--phone">
      <span class="contact__icon">
        <svg width="16" height="22" viewBox="0 0 16 22" aria-hidden="true">
          <rect x="1.5" y="1" width="13" height="20" rx="2" fill="none" stroke="var(--cyan)" stroke-width="2"/>
          <rect x="4" y="4" width="8" height="6" fill="var(--cyan)"/>
          <circle cx="8" cy="16" r="1.6" fill="var(--cyan)"/>
        </svg>
      </span>
      0400 213 594
    </div>

    <div class="contact contact--email">
      <span class="contact__icon">
        <svg width="22" height="16" viewBox="0 0 22 16" aria-hidden="true">
          <rect x="1" y="1" width="20" height="14" rx="1.5" fill="var(--cyan)"/>
          <polyline points="1,1.5 11,9 21,1.5" fill="none" stroke="var(--white)" stroke-width="1.6"/>
        </svg>
      </span>
      Liam@marshbuilding.com.au
    </div>

    <div class="contact contact--address">
      <span class="contact__icon">
        <svg width="16" height="22" viewBox="0 0 16 22" aria-hidden="true">
          <path d="M8 1C4.1 1 1 4.1 1 8c0 5 7 13 7 13s7-8 7-13c0-3.9-3.1-7-7-7z" fill="var(--cyan)"/>
          <circle cx="8" cy="8" r="2.6" fill="var(--white)"/>
        </svg>
      </span>
      14 Tarrant Rise<br>Harlow Bay WA 6290
    </div>
  </section>

  <section class="card card--back" aria-label="Business card back">
    <div class="back-brand">
      <span class="back-brand__mark"></span>
      <span class="back-brand__name">Marsh Building<br>&amp; Construction</span>
    </div>
  </section>
</main>
</body>
</html>
```